House-share and Room Rental Website (With Focus on the Bedroom Landing Page)

Looking for website design for our House-share (executive accommodation) and room rental business.

Our company name is: Lodgivo could also be written as LodGivo or lodgivo. Either is fine .. just looking for a nice clean catchy logo to go with the design.

EXAMPLES
These are examples of other websites in this field that are doing well. this is a kind of baseline.
https://nestpartners-example.com.au/
https://www.bunkora-example.com/
https://www.dwelzy-example.com/
https://www.habiquo-example.net/
https://www.cohabiscout-example.com.au/

Our business model is to rent rooms to people looking for high-quality accommodation. We fill the gap between those looking to rent rooms and those with rooms to rent. However, our model is slightly different from those already on the market as we looking to fill a massive gap in the market delivering upmarket rooms for rent.(Executive Accommodation) also in the back end will be coupled with a self management process in the back end.

We offer executive style accommodation that stands out above the rest. With special extras like fire safety.. and management processes that create happier homes. We are looking for a web design package that can help us grow and scale our business. We need a design that is captivating

Our MAIN focus is having a room landing page that stands out from the rest... The core of our business will rely on the promotion of the rooms in a share house... so the whole design relies on the BEDROOM landing page to drive results.

Target Market(s)

We have 2 markets we are aiming at ... the first market is people offering rooms to rent who want the highest rental return. The second market is people looking to rent safe, high-quality rooms, in houses that are well managed and looked after.

Industry/Entity Type

Share Economy

Logo Text

LodGivo

Number of Pages Required

5+ page

Font styles to use
Sans Serif

Colors
3276b5

Requirements
Must have
• A messaging system whereby we can create direct communication between those offering rooms and those looking for rooms.
• A call to action that says " Schedule an Inspection"
• Landing page for promoting rooms
• A home page for showing stock.
• Profile page for those selling rooms
• Profile page for those looking for rooms.
• A scheduling calendar for booking inspections
Nice to have
• Pages where new residents can lock in a room.. pay bond and rents.. and sign contracts
• Notifications
• SMS capabilities in the backend.
Should not have
• No script or handwriting fonts.

```html
<!DOCTYPE html>
<html lang="en">
<head>
<meta charset="utf-8">
<title>Lodgivo – Executive Accommodation</title>
<link rel="stylesheet" href="https://fonts.googleapis.com/css2?family=Cinzel:wght@400;600;700&family=Montserrat:wght@400;500;600&display=swap">
<style>
:root{
  --brand:#3276b5;
  --brand-dark:#255f96;
  --ink:#1d1d1d;
  --muted:#6b6b6b;
  --line:#d9d9d9;
  --page:#f6f6f6;
  --card:#ffffff;
  --footer:#232323;
  --footer-text:#cfcfcf;
  --gold:#f2b51f;
}
*{box-sizing:border-box;margin:0;padding:0}
html,body{width:1200px;height:3543px;overflow:hidden}
body{background:var(--page);font-family:"Montserrat",Arial,sans-serif;color:var(--ink);position:relative}
.abs{position:absolute}

/* Header */
.site-header{position:absolute;left:0;top:0;width:1200px;height:104px;background:#fff}
.menu-toggle{position:absolute;left:40px;top:42px;width:24px}
.menu-toggle span{display:block;height:3px;background:var(--ink);margin-bottom:5px}
.menu-toggle span:last-child{width:15px}
.brand{position:absolute;left:0;width:1200px;top:36px;text-align:center}
.brand-name{font-family:"Montserrat",Arial,sans-serif;font-weight:600;font-size:26px;color:var(--ink);letter-spacing:.5px}
.top-nav{position:absolute;right:48px;top:44px;display:flex;gap:44px;font-size:13px;font-weight:500}

/* Hero */
.hero{position:absolute;left:0;top:104px;width:1200px;height:671px;background:linear-gradient(100deg,#6b5443 0%,#b39478 25%,#ddd2c4 48%,#eef0f2 65%,#c9d4df 82%,#e9e5de 100%)}
.search-panel{position:absolute;left:40px;top:704px;width:1122px;height:163px;background:#fff;box-shadow:0 6px 18px rgba(0,0,0,.12);display:flex;align-items:center;padding:0 36px}
.field{width:172px}
.field label{display:block;font-size:11px;letter-spacing:.5px;color:#555;margin-bottom:22px}
.field label b{display:inline-block;width:9px;height:9px;border-radius:50%;background:#666;margin-left:4px;vertical-align:-1px}
.field .input{font-size:10px;color:#888;font-style:italic;border-bottom:1px solid var(--line);padding-bottom:8px;width:150px;position:relative}
.field .input em{position:absolute;right:0;top:0;font-style:normal;color:#888}
.btn{background:var(--brand);color:#fff;font-family:"Cinzel",Georgia,serif;font-size:12px;font-weight:600;letter-spacing:1px;text-align:center;border:2px solid var(--brand-dark)}
.search-btn{width:196px;height:50px;line-height:46px;margin-left:8px}

/* Section titles */
.section-title{position:absolute;left:0;width:1200px;text-align:center;font-family:"Cinzel",Georgia,serif;font-size:29px;font-weight:400;letter-spacing:1px}

/* Amenities */
.amenity{position:absolute;width:200px;text-align:center}
.amenity svg{display:block;margin:0 auto}
.amenity p{font-family:"Cinzel",Georgia,serif;font-size:13px;margin-top:14px}

/* Room cards */
.room-card{position:absolute;width:272px;height:414px;background:var(--card);box-shadow:0 1px 4px rgba(0,0,0,.06)}
.room-photo{height:170px}
.room-body{padding:22px 24px 0}
.room-title{font-family:"Cinzel",Georgia,serif;font-size:14px;font-weight:600;letter-spacing:.5px}
.room-addr{font-size:9.5px;margin-top:18px;display:flex;align-items:center;gap:6px;color:#333}
.room-stats{display:flex;margin-top:22px}
.stat{width:74px;font-size:9px;color:#555}
.stat .n{font-size:13px;color:var(--ink);margin-left:4px;vertical-align:4px}
.stat div{margin-top:4px}
.room-link{display:inline-block;margin-top:30px;font-family:"Cinzel",Georgia,serif;font-size:11px;font-weight:600;text-decoration:underline;color:#222}
.room-link.active{color:var(--brand)}

/* Testimonials */
.testimonials{position:absolute;left:0;top:2338px;width:1200px;height:333px;background:linear-gradient(90deg,#3a2c25 0%,#6d5a4e 30%,#4b3c34 60%,#2c221d 100%);color:#fff;text-align:center}
.testimonials h2{font-family:"Cinzel",Georgia,serif;font-weight:400;font-size:30px;margin-top:48px}
.testimonials .quote{font-size:11.5px;line-height:19px;width:640px;margin:14px auto 0}
.testimonials .author{font-family:"Cinzel",Georgia,serif;font-size:19px;margin-top:22px}
.stars{color:var(--gold);font-size:17px;letter-spacing:1px;margin-top:4px}
.dots{display:flex;justify-content:center;gap:10px;margin-top:8px}
.dots i{width:6px;height:6px;border-radius:50%;background:rgba(255,255,255,.5)}
.dots i.on{background:#fff}

/* Newsletter */
.news-input{position:absolute;left:245px;top:2832px;width:512px;height:50px;border:1px solid #999;background:#fff;font-size:11px;font-style:italic;padding:15px 24px;color:#444}
.news-btn{position:absolute;left:757px;top:2830px;width:196px;height:54px;line-height:50px}

/* Features */
.feature{position:absolute;width:300px;text-align:center}
.feature h3{font-family:"Cinzel",Georgia,serif;font-size:13px;font-weight:600;margin-top:16px}
.feature p{font-size:11px;line-height:14px;color:#333;margin-top:6px}

/* Footer */
.site-footer{position:absolute;left:0;top:3165px;width:1200px;height:378px;background:var(--footer);color:var(--footer-text)}
.footer-col{position:absolute;top:60px}
.footer-col h4{font-family:"Cinzel",Georgia,serif;font-weight:400;font-size:20px;color:#fff;letter-spacing:.5px;margin-bottom:28px}
.footer-brand{font-family:"Montserrat",Arial,sans-serif;font-weight:600;font-size:24px;color:#fff}
.footer-about{font-size:11px;font-style:italic;line-height:15px;color:#eee;margin-top:26px;width:240px}
.footer-more{font-size:11px;color:var(--brand);text-decoration:underline;margin-top:12px;font-family:"Cinzel",Georgia,serif}
.socials{display:flex;gap:24px;margin-top:44px}
.socials i{width:14px;height:14px;border-radius:50%;background:var(--brand);display:block}
.link-list{list-style:none;font-size:11px;line-height:21px}
.link-list li::before{content:"•";color:#888;margin-right:10px}
.contact-list{list-style:none;font-size:11px;line-height:28px}
.contact-list li{display:flex;align-items:center;gap:10px}
.contact-list li .dot{width:10px;height:10px;border-radius:50%;background:var(--brand)}
.qc-row{display:flex;gap:4px}
.qc-field{border:1px solid #999;height:32px;font-size:9px;font-style:italic;color:#fff;padding:9px 6px}
.qc-btn{width:312px;height:30px;line-height:28px;margin-top:8px;font-size:11px}
.footer-bottom{position:absolute;left:40px;top:3478px;width:1122px;font-size:10px;font-style:italic;color:#ddd;display:flex;justify-content:space-between;align-items:center}
.footer-bottom .rule{position:absolute;left:0;top:-14px;width:1122px;height:1px;background:#3a3a3a}
.cards{display:flex;gap:6px}
.cards i{width:28px;height:16px;background:#e8e8e8;border-radius:2px;display:block}
</style>
</head>
<body>

<header class="site-header">
  <div class="menu-toggle"><span></span><span></span><span></span></div>
  <div class="brand"><div class="brand-name">Lodgivo</div></div>
  <nav class="top-nav"><span>USD</span><span>EN</span><span>LOGIN</span><span>SIGN UP</span></nav>
</header>

<div class="hero" role="img" aria-label="Bright modern executive bedroom with a grey upholstered bed, wooden panel wall and window seat"></div>

<form class="search-panel">
  <div class="field"><label>LOCATION<b></b></label><div class="input">Select Location<em>⌄</em></div></div>
  <div class="field"><label>ROOM TYPE<b></b></label><div class="input">Single Room<em>⌄</em></div></div>
  <div class="field"><label>CHECK IN<b></b></label><div class="input">Select date<em>▦</em></div></div>
  <div class="field"><label>CHECK OUT<b></b></label><div class="input">Select date<em>▦</em></div></div>
  <div class="field"><label>GUESTS<b></b></label><div class="input">Number Of Guest<em>⌄</em></div></div>
  <div class="btn search-btn">SEARCH NOW</div>
</form>

<h2 class="section-title" style="top:938px">Public Amenities</h2>

<div class="amenity" style="left:77px;top:1030px">
  <svg width="64" height="64" viewBox="0 0 64 64" fill="none" stroke="#1d1d1d" stroke-width="2"><rect x="8" y="10" width="40" height="34" rx="8" fill="#3276b5"/><rect x="14" y="16" width="28" height="12" fill="#fff"/><rect x="26" y="30" width="32" height="22" rx="6" fill="#3276b5"/><rect x="31" y="35" width="22" height="8" fill="#fff"/><circle cx="16" cy="48" r="4" fill="#fff"/><circle cx="33" cy="54" r="3" fill="#fff"/><circle cx="51" cy="54" r="3" fill="#fff"/></svg>
  <p>Transport options</p>
</div>
<div class="amenity" style="left:290px;top:1030px">
  <svg width="64" height="64" viewBox="0 0 64 64" fill="none" stroke="#1d1d1d" stroke-width="2"><rect x="16" y="4" width="32" height="46" rx="6" fill="#3276b5"/><rect x="21" y="10" width="22" height="16" fill="#fff"/><circle cx="24" cy="38" r="3" fill="#fff"/><circle cx="40" cy="38" r="3" fill="#fff"/><path d="M22 50 14 60M42 50l8 10M18 56h28"/></svg>
  <p>Trains</p>
</div>
<div class="amenity" style="left:502px;top:1030px">
  <svg width="70" height="64" viewBox="0 0 70 64" fill="none" stroke="#1d1d1d" stroke-width="2"><rect x="4" y="16" width="62" height="30" rx="6" fill="#3276b5"/><path d="M10 22h10v10H10zM24 22h10v10H24zM38 22h10v10H38zM52 22h8v10h-8z" fill="#fff"/><circle cx="18" cy="48" r="5" fill="#fff"/><circle cx="52" cy="48" r="5" fill="#fff"/></svg>
  <p>Busses</p>
</div>
<div class="amenity" style="left:715px;top:1030px">
  <svg width="64" height="64" viewBox="0 0 64 64" fill="none" stroke="#1d1d1d" stroke-width="2"><circle cx="32" cy="32" r="26" fill="#3276b5"/><path d="M16 20c6 2 10 0 12 6s-6 8-4 14 8 2 10 10M40 12c-2 6 4 8 8 8s6 8 2 12" stroke="#fff"/><circle cx="46" cy="44" r="6" fill="#fff"/></svg>
  <p>Location Or Distance</p>
</div>
<div class="amenity" style="left:927px;top:1030px">
  <svg width="64" height="64" viewBox="0 0 64 64" fill="none" stroke="#1d1d1d" stroke-width="2"><path d="M6 14l16-6 20 6 16-6v42l-16 6-20-6-16 6z" fill="#3276b5"/><path d="M22 8v42M42 14v42"/><path d="M28 24c2 4 8 4 10 10" stroke="#fff"/></svg>
  <p>Map</p>
</div>

<h2 class="section-title" style="top:1214px">Recommended Bedrooms</h2>

<article class="room-card" style="left:40px;top:1306px">
  <div class="room-photo" role="img" aria-label="White minimalist bedroom with grey bedding" style="background:linear-gradient(135deg,#eef0f1,#c9ccce)"></div>
  <div class="room-body">
    <h3 class="room-title">Luxurious Bedroom</h3>
    <p class="room-addr"><svg width="10" height="13" viewBox="0 0 10 13"><path d="M5 1a4 4 0 0 1 4 4c0 3-4 7-4 7S1 8 1 5a4 4 0 0 1 4-4z" fill="none" stroke="#333"/><circle cx="5" cy="5" r="1.4" fill="#333"/></svg>14 Harbor Ln, Fairview, VT 20455 Australia</p>
    <div class="room-stats">
      <div class="stat"><svg width="18" height="18" viewBox="0 0 18 18" fill="none" stroke="#333"><rect x="2" y="2" width="14" height="14"/><path d="M2 9h14M9 2v14"/></svg><span class="n">2</span><div>Rooms</div></div>
      <div class="stat"><svg width="20" height="18" viewBox="0 0 20 18" fill="none" stroke="#333"><path d="M2 16V3h16v13M2 11h16M5 11V7h10v4"/></svg><span class="n">1</span><div>Bedroom</div></div>
      <div class="stat"><svg width="20" height="18" viewBox="0 0 20 18" fill="none" stroke="#333"><path d="M2 9h16v3a4 4 0 0 1-4 4H6a4 4 0 0 1-4-4zM4 9V4a2 2 0 0 1 4 0"/></svg><span class="n">1</span><div>Bathroom</div></div>
    </div>
    <a class="room-link active">Browse</a>
  </div>
</article>
<article class="room-card" style="left:324px;top:1306px">
  <div class="room-photo" role="img" aria-label="Bedroom with orange bedspread facing a beach view" style="background:linear-gradient(135deg,#e9ecee,#d88a3e 60%,#7d6a5a)"></div>
  <div class="room-body">
    <h3 class="room-title">Luxurious Bedroom</h3>
    <p class="room-addr"><svg width="10" height="13" viewBox="0 0 10 13"><path d="M5 1a4 4 0 0 1 4 4c0 3-4 7-4 7S1 8 1 5a4 4 0 0 1 4-4z" fill="none" stroke="#333"/><circle cx="5" cy="5" r="1.4" fill="#333"/></svg>14 Harbor Ln, Fairview, VT 20455 Australia</p>
    <div class="room-stats">
      <div class="stat"><svg width="18" height="18" viewBox="0 0 18 18" fill="none" stroke="#333"><rect x="2" y="2" width="14" height="14"/><path d="M2 9h14M9 2v14"/></svg><span class="n">3</span><div>Rooms</div></div>
      <div class="stat"><svg width="20" height="18" viewBox="0 0 20 18" fill="none" stroke="#333"><path d="M2 16V3h16v13M2 11h16M5 11V7h10v4"/></svg><span class="n">1</span><div>Bedroom</div></div>
      <div class="stat"><svg width="20" height="18" viewBox="0 0 20 18" fill="none" stroke="#333"><path d="M2 9h16v3a4 4 0 0 1-4 4H6a4 4 0 0 1-4-4zM4 9V4a2 2 0 0 1 4 0"/></svg><span class="n">2</span><div>Bathroom</div></div>
    </div>
    <a class="room-link">Browse</a>
  </div>
</article>
<article class="room-card" style="left:607px;top:1306px">
  <div class="room-photo" role="img" aria-label="Bedroom with dark feature wall and white bed" style="background:linear-gradient(135deg,#3c3c3c,#9b9b9b 55%,#6a4a38)"></div>
  <div class="room-body">
    <h3 class="room-title">Luxurious Bedroom</h3>
    <p class="room-addr"><svg width="10" height="13" viewBox="0 0 10 13"><path d="M5 1a4 4 0 0 1 4 4c0 3-4 7-4 7S1 8 1 5a4 4 0 0 1 4-4z" fill="none" stroke="#333"/><circle cx="5" cy="5" r="1.4" fill="#333"/></svg>14 Harbor Ln, Fairview, VT 20455 Australia</p>
    <div class="room-stats">
      <div class="stat"><svg width="18" height="18" viewBox="0 0 18 18" fill="none" stroke="#333"><rect x="2" y="2" width="14" height="14"/><path d="M2 9h14M9 2v14"/></svg><span class="n">4</span><div>Rooms</div></div>
      <div class="stat"><svg width="20" height="18" viewBox="0 0 20 18" fill="none" stroke="#333"><path d="M2 16V3h16v13M2 11h16M5 11V7h10v4"/></svg><span class="n">1</span><div>Bedroom</div></div>
      <div class="stat"><svg width="20" height="18" viewBox="0 0 20 18" fill="none" stroke="#333"><path d="M2 9h16v3a4 4 0 0 1-4 4H6a4 4 0 0 1-4-4zM4 9V4a2 2 0 0 1 4 0"/></svg><span class="n">1</span><div>Bathroom</div></div>
    </div>
    <a class="room-link">Browse</a>
  </div>
</article>
<article class="room-card" style="left:890px;top:1306px">
  <div class="room-photo" role="img" aria-label="Warmly lit bedroom with dark wooden bed frame" style="background:linear-gradient(135deg,#d8c4a2,#8a6a48 55%,#3a2a1e)"></div>
  <div class="room-body">
    <h3 class="room-title">Luxurious Bedroom</h3>
    <p class="room-addr"><svg width="10" height="13" viewBox="0 0 10 13"><path d="M5 1a4 4 0 0 1 4 4c0 3-4 7-4 7S1 8 1 5a4 4 0 0 1 4-4z" fill="none" stroke="#333"/><circle cx="5" cy="5" r="1.4" fill="#333"/></svg>14 Harbor Ln, Fairview, VT 20455 Australia</p>
    <div class="room-stats">
      <div class="stat"><svg width="18" height="18" viewBox="0 0 18 18" fill="none" stroke="#333"><rect x="2" y="2" width="14" height="14"/><path d="M2 9h14M9 2v14"/></svg><span class="n">3</span><div>Rooms</div></div>
      <div class="stat"><svg width="20" height="18" viewBox="0 0 20 18" fill="none" stroke="#333"><path d="M2 16V3h16v13M2 11h16M5 11V7h10v4"/></svg><span class="n">1</span><div>Bedroom</div></div>
      <div class="stat"><svg width="20" height="18" viewBox="0 0 20 18" fill="none" stroke="#333"><path d="M2 9h16v3a4 4 0 0 1-4 4H6a4 4 0 0 1-4-4zM4 9V4a2 2 0 0 1 4 0"/></svg><span class="n">1</span><div>Bathroom</div></div>
    </div>
    <a class="room-link">Browse</a>
  </div>
</article>

<article class="room-card" style="left:40px;top:1738px">
  <div class="room-photo" role="img" aria-label="Bright bedroom with black bed and wooden wardrobe" style="background:linear-gradient(135deg,#f1f1ef,#bdb7ae 60%,#5a3c28)"></div>
  <div class="room-body">
    <h3 class="room-title">Luxurious Bedroom</h3>
    <p class="room-addr"><svg width="10" height="13" viewBox="0 0 10 13"><path d="M5 1a4 4 0 0 1 4 4c0 3-4 7-4 7S1 8 1 5a4 4 0 0 1 4-4z" fill="none" stroke="#333"/><circle cx="5" cy="5" r="1.4" fill="#333"/></svg>14 Harbor Ln, Fairview, VT 20455 Australia</p>
    <div class="room-stats">
      <div class="stat"><svg width="18" height="18" viewBox="0 0 18 18" fill="none" stroke="#333"><rect x="2" y="2" width="14" height="14"/><path d="M2 9h14M9 2v14"/></svg><span class="n">4</span><div>Rooms</div></div>
      <div class="stat"><svg width="20" height="18" viewBox="0 0 20 18" fill="none" stroke="#333"><path d="M2 16V3h16v13M2 11h16M5 11V7h10v4"/></svg><span class="n">1</span><div>Bedroom</div></div>
      <div class="stat"><svg width="20" height="18" viewBox="0 0 20 18" fill="none" stroke="#333"><path d="M2 9h16v3a4 4 0 0 1-4 4H6a4 4 0 0 1-4-4zM4 9V4a2 2 0 0 1 4 0"/></svg><span class="n">2</span><div>Bathroom</div></div>
    </div>
    <a class="room-link">Browse</a>
  </div>
</article>
<article class="room-card" style="left:324px;top:1738px">
  <div class="room-photo" role="img" aria-label="Light Scandinavian bedroom with plants and wooden bed" style="background:linear-gradient(135deg,#ecebe6,#cfc3ae 55%,#8f9b7a)"></div>
  <div class="room-body">
    <h3 class="room-title">Luxurious Bedroom</h3>
    <p class="room-addr"><svg width="10" height="13" viewBox="0 0 10 13"><path d="M5 1a4 4 0 0 1 4 4c0 3-4 7-4 7S1 8 1 5a4 4 0 0 1 4-4z" fill="none" stroke="#333"/><circle cx="5" cy="5" r="1.4" fill="#333"/></svg>14 Harbor Ln, Fairview, VT 20455 Australia</p>
    <div class="room-stats">
      <div class="stat"><svg width="18" height="18" viewBox="0 0 18 18" fill="none" stroke="#333"><rect x="2" y="2" width="14" height="14"/><path d="M2 9h14M9 2v14"/></svg><span class="n">3</span><div>Rooms</div></div>
      <div class="stat"><svg width="20" height="18" viewBox="0 0 20 18" fill="none" stroke="#333"><path d="M2 16V3h16v13M2 11h16M5 11V7h10v4"/></svg><span class="n">1</span><div>Bedroom</div></div>
      <div class="stat"><svg width="20" height="18" viewBox="0 0 20 18" fill="none" stroke="#333"><path d="M2 9h16v3a4 4 0 0 1-4 4H6a4 4 0 0 1-4-4zM4 9V4a2 2 0 0 1 4 0"/></svg><span class="n">1</span><div>Bathroom</div></div>
    </div>
    <a class="room-link">Browse</a>
  </div>
</article>
<article class="room-card" style="left:607px;top:1738px">
  <div class="room-photo" role="img" aria-label="Compact bedroom with blue and white bedding and dark floor" style="background:linear-gradient(135deg,#d9d6d0,#8c96a8 55%,#3b302a)"></div>
  <div class="room-body">
    <h3 class="room-title">Luxurious Bedroom</h3>
    <p class="room-addr"><svg width="10" height="13" viewBox="0 0 10 13"><path d="M5 1a4 4 0 0 1 4 4c0 3-4 7-4 7S1 8 1 5a4 4 0 0 1 4-4z" fill="none" stroke="#333"/><circle cx="5" cy="5" r="1.4" fill="#333"/></svg>14 Harbor Ln, Fairview, VT 20455 Australia</p>
    <div class="room-stats">
      <div class="stat"><svg width="18" height="18" viewBox="0 0 18 18" fill="none" stroke="#333"><rect x="2" y="2" width="14" height="14"/><path d="M2 9h14M9 2v14"/></svg><span class="n">2</span><div>Rooms</div></div>
      <div class="stat"><svg width="20" height="18" viewBox="0 0 20 18" fill="none" stroke="#333"><path d="M2 16V3h16v13M2 11h16M5 11V7h10v4"/></svg><span class="n">1</span><div>Bedroom</div></div>
      <div class="stat"><svg width="20" height="18" viewBox="0 0 20 18" fill="none" stroke="#333"><path d="M2 9h16v3a4 4 0 0 1-4 4H6a4 4 0 0 1-4-4zM4 9V4a2 2 0 0 1 4 0"/></svg><span class="n">1</span><div>Bathroom</div></div>
    </div>
    <a class="room-link">Browse</a>
  </div>
</article>
<article class="room-card" style="left:890px;top:1738px">
  <div class="room-photo" role="img" aria-label="Bedroom with wooden plank feature wall and grey bed" style="background:linear-gradient(135deg,#2a2624,#7a6456 50%,#b9aea3)"></div>
  <div class="room-body">
    <h3 class="room-title">Luxurious Bedroom</h3>
    <p class="room-addr"><svg width="10" height="13" viewBox="0 0 10 13"><path d="M5 1a4 4 0 0 1 4 4c0 3-4 7-4 7S1 8 1 5a4 4 0 0 1 4-4z" fill="none" stroke="#333"/><circle cx="5" cy="5" r="1.4" fill="#333"/></svg>14 Harbor Ln, Fairview, VT 20455 Australia</p>
    <div class="room-stats">
      <div class="stat"><svg width="18" height="18" viewBox="0 0 18 18" fill="none" stroke="#333"><rect x="2" y="2" width="14" height="14"/><path d="M2 9h14M9 2v14"/></svg><span class="n">3</span><div>Rooms</div></div>
      <div class="stat"><svg width="20" height="18" viewBox="0 0 20 18" fill="none" stroke="#333"><path d="M2 16V3h16v13M2 11h16M5 11V7h10v4"/></svg><span class="n">1</span><div>Bedroom</div></div>
      <div class="stat"><svg width="20" height="18" viewBox="0 0 20 18" fill="none" stroke="#333"><path d="M2 9h16v3a4 4 0 0 1-4 4H6a4 4 0 0 1-4-4zM4 9V4a2 2 0 0 1 4 0"/></svg><span class="n">1</span><div>Bathroom</div></div>
    </div>
    <a class="room-link">Browse</a>
  </div>
</article>

<div class="btn abs" style="left:501px;top:2225px;width:196px;height:50px;line-height:46px">BROWSE MORE</div>

<section class="testimonials" role="img" aria-label="Dimly lit hotel bedroom with patterned bed runner behind client testimonial">
  <h2>Our Clients Say`s</h2>
  <p class="quote">Lorem Ipsum is simply dummy text of the printing and typesetting industry. Lorem Ipsum has been the industry's standard dummy text ever since the 1500s.</p>
  <p class="author">Dana Hollis</p>
  <div class="stars">★★★★★</div>
  <div class="dots"><i></i><i></i><i class="on"></i><i></i></div>
</section>

<h2 class="section-title" style="top:2742px">Subscribe Our Newsletter</h2>
<div class="news-input">Email Address</div>
<div class="btn news-btn">BROWSE MORE</div>

<div class="feature" style="left:87px;top:2950px">
  <svg width="60" height="60" viewBox="0 0 60 60" style="display:block;margin:0 auto"><circle cx="32" cy="28" r="20" fill="#3276b5" stroke="#1d1d1d" stroke-width="2"/><text x="32" y="35" text-anchor="middle" font-family="Montserrat,sans-serif" font-weight="600" font-size="18" fill="#fff">24</text><path d="M6 36c2 10 10 18 20 20l4-6-6-4-3 3c-4-2-7-5-9-9l3-3-4-6z" fill="#3276b5" stroke="#1d1d1d" stroke-width="2"/></svg>
  <h3>24/7 Customer Support</h3>
  <p>Lorem Ipsum is simply dummy text of the<br>printing and typesetting industry.</p>
</div>
<div class="feature" style="left:450px;top:2950px">
  <svg width="60" height="60" viewBox="0 0 60 60" style="display:block;margin:0 auto" fill="none" stroke="#1d1d1d" stroke-width="2"><circle cx="30" cy="26" r="18" fill="#3276b5"/><path d="M16 18c6 2 10 0 12 6s-4 8-2 14M38 12c-2 6 4 8 6 12" stroke="#fff"/><path d="M30 44v8M20 54h20M12 24a18 18 0 0 0 30 16"/></svg>
  <h3>Global hospitality standards</h3>
  <p>Lorem Ipsum is simply dummy text of the<br>printing and typesetting industry.</p>
</div>
<div class="feature" style="left:813px;top:2950px">
  <svg width="70" height="60" viewBox="0 0 70 60" style="display:block;margin:0 auto" stroke="#1d1d1d" stroke-width="2"><path d="M35 8l6 14 15 1-12 9 4 15-13-8-13 8 4-15-12-9 15-1z" fill="#3276b5"/><path d="M12 28l2 5 5 .5-4 3 1.5 5-4.5-3-4.5 3 1.5-5-4-3 5-.5zM58 28l2 5 5 .5-4 3 1.5 5-4.5-3-4.5 3 1.5-5-4-3 5-.5z" fill="#3276b5"/></svg>
  <h3>5-star hosts</h3>
  <p>Lorem Ipsum is simply dummy text of the<br>printing and typesetting industry.</p>
</div>

<footer class="site-footer">
  <div class="footer-col" style="left:40px;top:44px">
    <div class="footer-brand">Lodgivo</div>
    <p class="footer-about">Lorem Ipsum is simply dummy text of the printing and typesetting industry.</p>
    <p class="footer-more">Read More</p>
    <div class="socials"><i></i><i></i><i></i><i></i><i></i></div>
  </div>
  <div class="footer-col" style="left:355px">
    <h4>Useful Link</h4>
    <ul class="link-list"><li>Login</li><li>Register</li><li>My Profile</li><li>My Subscription</li><li>Privacy Policy</li><li>Term &amp; condition</li></ul>
  </div>
  <div class="footer-col" style="left:593px">
    <h4>Contact Info</h4>
    <ul class="contact-list">
      <li><span class="dot"></span>(+000) 555 0142</li>
      <li><span class="dot"></span>(+000) 555 0142</li>
      <li><span class="dot"></span>info@lodgivo.com</li>
      <li><span class="dot"></span>418 Elmwood Avenue</li>
      <li style="padding-left:20px">Brookdale, NV 20611</li>
    </ul>
  </div>
  <div class="footer-col" style="left:851px">
    <h4>Qucik Contact</h4>
    <div class="qc-row"><div class="qc-field" style="width:154px">Full Name</div><div class="qc-field" style="width:154px">Email Address</div></div>
    <div class="qc-field" style="width:312px;height:56px;margin-top:2px">Message</div>
    <div class="btn qc-btn">SUBMIT NOW</div>
  </div>
</footer>

<div class="footer-bottom">
  <span class="rule"></span>
  <span>Copyright © 2019 Lodgivo. All rights reserved.</span>
  <span class="cards"><i></i><i></i><i></i><i></i><i></i></span>
</div>

</body>
</html>
```